Orvane Group Business Card

Building Management company based in Sydney, Australia. We provide onsite management for commercial and residential buildings.
I would like a sophisticated minimalist design that indicates that we provide a high-end service. I would like a silver or metal look background or something similar.
The business card should have:
Name
Title
email
Office Phone
Mobile
Address
Website
The services that we provide should be prominent:
Building Management - Concierge - Caretaking - Cleaning

```html
<!DOCTYPE html>
<html lang="en">
<head>
<meta charset="utf-8">
<title>Orvane Group Business Card</title>
<link href="https://fonts.googleapis.com/css2?family=Lato:wght@400;700;900&display=swap" rel="stylesheet">
<style>
  :root {
    --stage: #2b2b2b;
    --card-light: #f7f7f7;
    --card-mid: #e4e4e6;
    --ink: #1f1f1f;
    --band: #0d0d0d;
    --blue: #1f74c9;
    --sky: #2a9fe0;
    --white: #ffffff;
  }
  * { box-sizing: border-box; margin: 0; padding: 0; }
  html, body { width: 1200px; height: 873px; overflow: hidden; }
  body {
    background: var(--stage);
    font-family: "Lato", sans-serif;
    position: relative;
  }
  .card {
    position: absolute;
    width: 500px;
    height: 286px;
    border-radius: 22px;
    overflow: hidden;
    background: linear-gradient(135deg, var(--white) 0%, var(--card-light) 40%, var(--card-mid) 100%);
  }
  .card-front { left: 90px; top: 110px; }
  .card-back { left: 610px; top: 470px; }
  .card-art { position: absolute; inset: 0; width: 100%; height: 100%; }
  .brand {
    position: absolute;
    display: flex;
    align-items: center;
    gap: 10px;
    font-weight: 900;
    color: var(--ink);
    letter-spacing: 1px;
    white-space: nowrap;
  }
  .brand-mark { width: 14px; height: 14px; background: var(--blue); }
  .card-front .brand { left: 50px; top: 100px; font-size: 32px; }
  .card-back .brand { right: 28px; top: 60px; font-size: 24px; }
  .person { position: absolute; left: 28px; top: 42px; }
  .person-name { font-size: 24px; font-weight: 700; color: var(--ink); }
  .person-title { font-size: 14px; font-weight: 700; color: var(--blue); margin-top: 2px; }
  .contact-list {
    position: absolute;
    left: 28px;
    top: 196px;
    list-style: none;
  }
  .contact-item {
    display: flex;
    align-items: center;
    gap: 12px;
    color: var(--white);
    font-size: 14px;
    line-height: 21px;
  }
  .contact-icon { width: 12px; height: 12px; flex: none; }
  .services-text { font-family: "Lato", sans-serif; font-size: 11px; fill: var(--white); }
</style>
</head>
<body>

<section class="card card-front" aria-label="Card front">
  <svg class="card-art" viewBox="0 0 500 286">
    <path d="M225 286 Q330 140 500 62 L500 286 Z" fill="var(--band)"/>
    <path id="services-curve" d="M246 282 Q345 156 500 86" fill="none"/>
    <path d="M205 286 Q315 128 500 52" fill="none" stroke="var(--sky)" stroke-width="5"/>
    <text class="services-text"><textPath href="#services-curve" startOffset="2%">Building Management - Concierge - Caretaking - Cleaning</textPath></text>
  </svg>
  <div class="brand"><span class="brand-mark"></span>ORVANE GROUP</div>
</section>

<section class="card card-back" aria-label="Card back">
  <svg class="card-art" viewBox="0 0 500 286">
    <path d="M0 196 Q250 118 500 168 L500 286 L0 286 Z" fill="var(--band)"/>
    <path d="M0 186 Q245 106 460 142" fill="none" stroke="var(--blue)" stroke-width="7"/>
  </svg>
  <div class="person">
    <p class="person-name">Daniel Reyes</p>
    <p class="person-title">Director</p>
  </div>
  <div class="brand"><span class="brand-mark"></span>ORVANE GROUP</div>
  <ul class="contact-list">
    <li class="contact-item">
      <svg class="contact-icon" viewBox="0 0 12 12"><rect x="3" y="0.5" width="6" height="11" rx="1" fill="none" stroke="var(--blue)" stroke-width="1.3"/></svg>
      +61 (0) 412 55 0198
    </li>
    <li class="contact-item">
      <svg class="contact-icon" viewBox="0 0 12 12"><path d="M1 4 Q6 0 11 4 L9 6 L7.5 4.5 L4.5 4.5 L3 6 Z" fill="var(--blue)"/><rect x="2" y="7" width="8" height="4" rx="1" fill="var(--blue)"/></svg>
      +61 (0)2 9000 4417
    </li>
    <li class="contact-item">
      <svg class="contact-icon" viewBox="0 0 12 12"><rect x="0.5" y="2.5" width="11" height="7" fill="var(--blue)"/><path d="M0.5 2.5 L6 7 L11.5 2.5" fill="none" stroke="var(--band)" stroke-width="1"/></svg>
      daniel@orvanegroup.com
    </li>
    <li class="contact-item">
      <svg class="contact-icon" viewBox="0 0 12 12"><circle cx="6" cy="6" r="5" fill="none" stroke="var(--blue)" stroke-width="1.4"/><line x1="1" y1="6" x2="11" y2="6" stroke="var(--blue)" stroke-width="1"/></svg>
      www.orvanegroup.com
    </li>
  </ul>
</section>

</body>
</html>
```